Business Card Design Project - del varosi group

dear Sirs

we need business card design for our group ( DEL Varosi Group ) , i have got the Logo design of our group from pixel harbor in previous , so all need details relating to our group i think available with you, as well as the the chosen logo design

we hope to provide us with business card logo that to be appropaite and satisfactory to us .

thanks

note : logo design of our group is attached .
Updates

Reason: please extend the deadline of my project for additional 15 days because i didn't received appropriate design for our gruop yet . kindly beaware that i have received 77 design till now , supossed to send me 200-250 design at least . thanks

Target Market(s)

contents

name : Kerem EL Nadiri

position : Operation Manager

Industry/Entity Type

Business

Requirements
Must have

• person name

group logo
Nice to have
• logo color matching with back background

```html
<!DOCTYPE html>
<html lang="en">
<head>
<meta charset="utf-8">
<title>DEL Varosi Group – Business Card</title>
<link rel="stylesheet" href="https://fonts.googleapis.com/css2?family=Montserrat:wght@600&family=Open+Sans:wght@400;600&display=swap">
<style>
  :root {
    --bg: #e9e7e3;
    --card: #ffffff;
    --card-sheen: #eef0f3;
    --blue: #1f5fa8;
    --blue-light: #2f78c6;
    --ink: #1c1c1c;
    --on-blue: #ffffff;
  }
  * { margin: 0; padding: 0; box-sizing: border-box; }
  html, body { width: 1200px; height: 900px; overflow: hidden; }
  body {
    background: var(--bg);
    font-family: "Open Sans", Arial, sans-serif;
    display: flex;
    flex-direction: column;
    align-items: center;
    justify-content: center;
    gap: 60px;
  }
  .card {
    position: relative;
    width: 620px;
    height: 355px;
    background: linear-gradient(120deg, var(--card) 0%, var(--card-sheen) 45%, var(--card) 60%, var(--card-sheen) 100%);
    box-shadow: 0 6px 18px rgba(0,0,0,0.18);
    overflow: hidden;
  }
  .brand {
    display: flex;
    align-items: center;
    gap: 12px;
  }
  .brand-mark {
    width: 22px;
    height: 22px;
    background: var(--blue);
  }
  .brand-name {
    font-family: "Montserrat", Arial, sans-serif;
    font-weight: 600;
    color: var(--blue);
    text-transform: uppercase;
    letter-spacing: 1px;
  }

  /* Front */
  .card-front { display: flex; flex-direction: column; align-items: center; justify-content: center; gap: 26px; }
  .card-front .brand-name { font-size: 40px; }
  .card-front .brand-mark { width: 30px; height: 30px; }
  .website { font-size: 13px; color: var(--ink); letter-spacing: 1.5px; }

  /* Back */
  .card-back .band { position: absolute; inset: 0; }
  .card-back .brand { position: absolute; left: 36px; top: 70px; }
  .card-back .brand-name { font-size: 26px; }
  .person { position: absolute; left: 40px; top: 252px; color: var(--on-blue); }
  .person-name { font-size: 17px; font-weight: 600; }
  .person-role { font-size: 11px; margin-bottom: 8px; }
  .person-address { font-size: 10.5px; line-height: 1.45; }
  .contacts {
    position: absolute; left: 440px; top: 70px;
    list-style: none; color: var(--on-blue); font-size: 11.5px;
  }
  .contacts li { display: flex; align-items: center; gap: 9px; height: 26px; }
  .contacts svg { width: 14px; height: 14px; fill: var(--on-blue); flex: none; }
</style>
</head>
<body>

<section class="card card-front" aria-label="Business card front">
  <div class="brand">
    <span class="brand-mark"></span>
    <span class="brand-name">DEL Varosi Group</span>
  </div>
  <p class="website">www.delvarosigroup.com</p>
</section>

<section class="card card-back" aria-label="Business card back">
  <svg class="band" viewBox="0 0 620 355" preserveAspectRatio="none" aria-hidden="true">
    <defs>
      <linearGradient id="blueBand" x1="0" y1="1" x2="1" y2="0">
        <stop offset="0" stop-color="#1f5fa8"/>
        <stop offset="1" stop-color="#2f78c6"/>
      </linearGradient>
    </defs>
    <polygon fill="url(#blueBand)" points="0,232 150,232 166,214 182,232 370,232 430,0 620,0 620,355 0,355"/>
  </svg>

  <div class="brand">
    <span class="brand-mark"></span>
    <span class="brand-name">DEL Varosi Group</span>
  </div>

  <div class="person">
    <p class="person-name">Kerem EL Nadiri</p>
    <p class="person-role">Operation Manager</p>
    <p class="person-address">DEL Varosi Group<br>14 Harlow St Brookvale,<br>QLD 0000</p>
  </div>

  <ul class="contacts">
    <li><svg viewBox="0 0 16 16"><path d="M2 3h4l1 3-2 1a8 8 0 0 0 4 4l1-2 3 1v4a1 1 0 0 1-1 1A12 12 0 0 1 1 4a1 1 0 0 1 1-1z"/></svg>0000 555 2020</li>
    <li><svg viewBox="0 0 16 16"><rect x="4" y="1" width="8" height="14" rx="1.5"/><rect x="5.5" y="3" width="5" height="8" fill="#1f5fa8"/></svg>0000 555 2020</li>
    <li><svg viewBox="0 0 16 16"><rect x="4" y="1" width="8" height="5"/><rect x="1" y="6" width="14" height="7" rx="1"/><rect x="4" y="10" width="8" height="5"/></svg>0000 555 2020</li>
    <li><svg viewBox="0 0 16 16"><path d="M1 4h14v9H1z"/><path d="M1 4l7 5 7-5" fill="none" stroke="#1f5fa8" stroke-width="1.3"/></svg>kerem@delvarosigroup.com</li>
    <li><svg viewBox="0 0 16 16"><circle cx="8" cy="8" r="7"/><path d="M1 8h14M8 1c-3 3-3 11 0 14M8 1c3 3 3 11 0 14" fill="none" stroke="#1f5fa8" stroke-width="1"/></svg>www.delvarosigroup.com</li>
  </ul>
</section>

</body>
</html>
```